Brightfen Business Card Redesign & Logo Update

We need to update our business cards to something more modern and fresh. Brightfen can provide the current color schemes and old design examples, but welcome creativity in helping us with this redesign. PLEASE NOTE that we no longer utilize the "tree" and/or "leaf" imagery in our branding. If able would apprecaite an update on the quality of our "words only" logo in Ai. / PNG formats too.

Target Market(s)

Investors, landowners, corporate partners, contractors

Industry/Entity Type

Environmental Restoration & Conservation

Contact Information for Business Card

Logo, persons name, title, mailing address, phone and email, website url

Font styles to use
Other font styles liked:
• Merriweather

Requirements
Nice to have
• Logo, persons name, title, mailing address, phone and email, website url, but open to ideams
Should not have
• No all back backgrounds

```html
<!DOCTYPE html>
<html lang="en">
<head>
<meta charset="utf-8">
<title>Brightfen Business Card</title>
<link rel="stylesheet" href="https://fonts.googleapis.com/css2?family=Oswald:wght@400;500;600&display=swap">
<style>
  :root{
    --stage:#1f1f1f;
    --paper:#ffffff;
    --ink:#151515;
    --orange:#ef7d0a;
    --green:#137d39;
    --green-deep:#0a4a20;
  }
  *{margin:0;padding:0;box-sizing:border-box}
  html,body{width:1093px;height:1200px;overflow:hidden;background:var(--stage)}
  body{position:relative;font-family:"Oswald",sans-serif;color:var(--ink)}
  .card{position:absolute;left:265px;border-radius:30px;overflow:hidden}
  .card-front{top:226px;width:577px;height:356px;background:var(--paper)}
  .card-back{top:621px;width:581px;height:357px;background:var(--green)}

  .holder{position:absolute;left:33px;top:66px;line-height:1}
  .holder-name{font-size:31px;font-weight:500;letter-spacing:-0.5px;text-transform:uppercase}
  .holder-name .first{color:var(--orange)}
  .holder-name .last{color:var(--green)}
  .holder-title{font-size:20px;font-weight:400;margin-top:-1px;letter-spacing:-0.3px}

  .wordmark{position:absolute;text-align:center;line-height:1;white-space:nowrap}
  .wordmark-name{font-weight:600;text-transform:uppercase}
  .wordmark-line{font-weight:500;text-transform:uppercase;letter-spacing:-0.3px}
  .card-front .wordmark{left:268px;width:274px;top:50px}
  .card-front .wordmark-name{font-size:58px;letter-spacing:-0.5px;color:var(--green)}
  .card-front .wordmark-line{font-size:18.5px;margin-top:3px}
  .card-back .wordmark{left:0;width:100%;top:124px}
  .card-back .wordmark-name{font-size:69px;letter-spacing:-0.3px;color:var(--green-deep)}
  .card-back .wordmark-line{font-size:22px;color:var(--green-deep);margin-top:3px}

  .contacts{position:absolute;left:33px;top:256px;list-style:none}
  .contacts li{display:flex;align-items:center;height:21px;font-size:19px;letter-spacing:-0.4px}
  .contacts svg{width:15px;height:15px;margin-right:8px;flex:none}
  .address{position:absolute;right:37px;top:280px;text-align:right;font-size:19px;line-height:21px;letter-spacing:-0.4px;font-style:normal}
</style>
</head>
<body>
  <section class="card card-front">
    <div class="holder">
      <p class="holder-name"><span class="first">Daniel</span> <span class="last">Harper</span></p>
      <p class="holder-title">Managing Director</p>
    </div>
    <div class="wordmark">
      <p class="wordmark-name">Brightfen</p>
      <p class="wordmark-line">Environmental Credit Company</p>
    </div>
    <ul class="contacts">
      <li><svg viewBox="0 0 16 16"><path d="M4 1.5l2.3 3-1.4 1.6c.8 1.9 2.2 3.3 4.1 4.1l1.6-1.4 3 2.3-1.3 2.4C7 13.2 2.8 9 2.1 2.8z" fill="none" stroke="#ef7d0a" stroke-width="1.6" stroke-linejoin="round"/></svg>055-842 317 604</li>
      <li><svg viewBox="0 0 16 16"><rect x="1" y="3" width="14" height="10" fill="#ef7d0a"/><path d="M1 3l7 6 7-6M1 13l5-5M15 13l-5-5" stroke="#fff" stroke-width="1.2" fill="none"/></svg>hello@brightfen.com</li>
      <li><svg viewBox="0 0 16 16"><g fill="none" stroke="#ef7d0a" stroke-width="1.3"><circle cx="8" cy="8" r="6.5"/><ellipse cx="8" cy="8" rx="3" ry="6.5"/><path d="M1.5 8h13M2.5 4.8h11M2.5 11.2h11"/></g></svg>www.brightfen.com</li>
    </ul>
    <address class="address">78, Marsh Lane Road<br>31720, Fenland</address>
  </section>

  <section class="card card-back">
    <div class="wordmark">
      <p class="wordmark-name">Brightfen</p>
      <p class="wordmark-line">Environmental Credit Company</p>
    </div>
  </section>
</body>
</html>
```